Business Card Design For A Renovation Contractor Company

We need a business card for a new company based in Singapore, our company name is "RB Tolvane". We are a renovation contractor that builds designs into reality. We build more of F&B restaurants, retail stores and commercial offices. We work very closely with designers. The final design should communicate to our client that we are a company that you can trust, that will plan and complete your project without giving you a headache. I like my client to remember my company as "RB". The beauty of SIMPLE is important.

Industry/Entity Type

Contractor

Requirements
Nice to have
• Black or Red base

```html
<!DOCTYPE html>
<html lang="en">
<head>
<meta charset="utf-8">
<title>RB Tolvane — Business Card Set</title>
<link rel="stylesheet" href="https://fonts.googleapis.com/css2?family=Open+Sans:wght@400;600&display=swap">
<style>
  :root {
    --stage: #3a2b23;
    --red: #e91c24;
    --charcoal: #1d2529;
    --slate: #5a6670;
    --ink: #231f20;
    --paper: #ffffff;
    --label: #f4f1ee;
  }
  * { box-sizing: border-box; margin: 0; padding: 0; }
  html, body { width: 1200px; height: 913px; overflow: hidden; }
  body {
    position: relative;
    background: var(--stage);
    font-family: "Open Sans", Arial, sans-serif;
  }
  .card {
    position: absolute;
    width: 464px;
    height: 266px;
    overflow: hidden;
    box-shadow: 0 4px 10px rgba(0,0,0,.45);
  }
  .option-label {
    position: absolute;
    color: var(--label);
    font-size: 28px;
    font-weight: 400;
  }

  /* Plain colour bands */
  .band { position: absolute; left: 0; width: 100%; }

  /* Front */
  .card--front { left: 90px; top: 146px; background: var(--paper); }
  .card--front .band--red { top: 0; height: 62px; background: var(--red); }
  .card--front .band--dark { top: 62px; height: 8px; background: var(--charcoal); }
  .holder {
    position: absolute; left: 30px; top: 18px;
    color: var(--paper); font-size: 23px; z-index: 2;
  }
  .holder small { font-size: 14px; }
  .contacts {
    position: absolute; left: 30px; bottom: 36px;
    list-style: none; font-size: 11px; color: var(--ink); line-height: 16px;
  }
  .contacts li { display: flex; align-items: center; gap: 7px; }
  .contacts svg { width: 10px; height: 10px; fill: var(--red); }

  /* Brand block */
  .brand { position: absolute; display: flex; flex-direction: column; align-items: center; }
  .brand__mark { border-radius: 50%; border: 4px solid currentColor; }
  .brand__name { font-weight: 400; line-height: 1.05; letter-spacing: .5px; }
  .brand__tagline { border-top: 1px solid currentColor; line-height: 1.25; padding-top: 1px; }

  .card--front .brand { right: 28px; top: 98px; color: var(--ink); }
  .card--front .brand__mark { width: 60px; height: 60px; color: var(--red); margin-bottom: 6px; }
  .card--front .brand__name { font-size: 38px; color: var(--ink); }
  .card--front .brand__tagline { font-size: 14px; }

  /* Back 1 */
  .card--back-dark { left: 584px; top: 143px; background: var(--charcoal); }
  .card--back-dark .band--slate { bottom: 34px; height: 8px; background: var(--slate); }
  .card--back-dark .band--red { bottom: 0; height: 34px; background: var(--red); }
  .site {
    position: absolute; top: 34px; width: 100%; text-align: center;
    color: #dfe3e5; font-size: 13px; letter-spacing: 4px;
  }

  /* Back 2 */
  .card--back-red { left: 91px; top: 437px; background: var(--red); }
  .card--back-red .brand { left: 0; right: 0; top: 50px; color: var(--paper); }
  .card--back-red .brand__mark { width: 80px; height: 80px; margin-bottom: 10px; }
  .card--back-red .brand__name { font-size: 46px; }
  .card--back-red .brand__tagline { font-size: 17px; border-top: none; }

  /* Back 3 */
  .card--back-white { left: 591px; top: 434px; background: var(--paper); }
  .card--back-white .brand { left: 0; right: 0; top: 62px; color: var(--ink); }
  .card--back-white .brand__mark { width: 66px; height: 66px; color: var(--red); margin-bottom: 6px; }
  .card--back-white .brand__name { font-size: 40px; }
  .card--back-white .brand__tagline { font-size: 14px; }
</style>
</head>
<body>

  <span class="option-label" style="left:945px; top:92px;">Back 1</span>
  <span class="option-label" style="left:127px; top:736px;">Back 2</span>
  <span class="option-label" style="left:980px; top:733px;">Back 3</span>

  <section class="card card--front">
    <div class="band band--red"></div>
    <div class="band band--dark"></div>
    <p class="holder">Your name, <small>Director</small></p>
    <ul class="contacts">
      <li><svg viewBox="0 0 10 10"><path d="M2,0 L4,2 L3,3.5 C4,5.5 4.5,6 6.5,7 L8,6 L10,8 L8,10 C4,9.5 .5,6 0,2 Z"/></svg>012.555.0142</li>
      <li><svg viewBox="0 0 10 10"><path d="M0,2 H10 V8 H0 Z M0,2 L5,6 L10,2" stroke="#fff" stroke-width=".8"/></svg>info@rbtolvane.com</li>
      <li><svg viewBox="0 0 10 10"><circle cx="5" cy="5" r="5"/></svg>www.rbtolvane.com</li>
    </ul>
    <div class="brand">
      <span class="brand__mark"></span>
      <span class="brand__name">RB Tolvane</span>
      <span class="brand__tagline">plans made real, built right</span>
    </div>
  </section>

  <section class="card card--back-dark">
    <p class="site">www.rbtolvane.com</p>
    <div class="band band--slate"></div>
    <div class="band band--red"></div>
  </section>

  <section class="card card--back-red">
    <div class="brand">
      <span class="brand__mark"></span>
      <span class="brand__name">RB Tolvane</span>
      <span class="brand__tagline">plans made real, built right</span>
    </div>
  </section>

  <section class="card card--back-white">
    <div class="brand">
      <span class="brand__mark"></span>
      <span class="brand__name">RB Tolvane</span>
      <span class="brand__tagline">plans made real, built right</span>
    </div>
  </section>

</body>
</html>
```